Brell Stone Company Business Cards

Front and Back Business Card - logo and text setup - cool design. I need workable photoshop or illustrator files so I can setup each employee card with design that is created
Updates

Hi everyone, thank you for the great entries. Please no more white and blue cards - there are so many already - black and silver only now please. thanks!

Target Market(s)

Construction Industry - Facility Managers

Industry/Entity Type

Construction

Contact Information for Business Card

I really like contemporary simplistic looks - clean neat....not opposed to seeing some black backrounds

Requirements
Must have
• Logo/website address with design on front only - www.brellstone-example.com (logo attached)
• Back:
• Name/Title/Company Address/Phone/email address
Nice to have
• Cool design
Should not have
• Nothing gimmicky like Fire or Water - since we are a Fire Protection company - it has all been done

```html
<!DOCTYPE html>
<html lang="en">
<head>
<meta charset="utf-8">
<title>Brell Stone Company Business Cards</title>
<link rel="stylesheet" href="https://fonts.googleapis.com/css2?family=Open+Sans:wght@400;600;700;800&display=swap">
<style>
  :root {
    --backdrop: #1d1d1f;
    --card-dark: #0d0d0e;
    --card-mid: #2a2a2c;
    --card-sheen: #4a4a4d;
    --ink-white: #f2f2f2;
    --ink-soft: #d8d8d8;
    --brand-red: #f0232a;
    --band-light: #f6c1c4;
    --divider: #5a5a5e;
  }
  * { margin: 0; padding: 0; box-sizing: border-box; }
  html, body {
    width: 1200px; height: 960px; overflow: hidden;
    background: var(--backdrop);
    font-family: "Open Sans", Arial, sans-serif;
  }
  .stage {
    position: relative; width: 1200px; height: 960px;
    display: flex; flex-direction: column; align-items: center; justify-content: center; gap: 70px;
  }
  .card {
    position: relative; width: 600px; height: 343px; border-radius: 4px; overflow: hidden;
    background:
      linear-gradient(115deg, transparent 40%, rgba(255,255,255,0.10) 55%, transparent 68%),
      repeating-linear-gradient(0deg, rgba(255,255,255,0.02) 0 1px, transparent 1px 3px),
      linear-gradient(135deg, var(--card-dark) 0%, var(--card-mid) 55%, var(--card-dark) 100%);
    box-shadow: 0 18px 40px rgba(0,0,0,0.55);
  }
  .brand-name {
    font-weight: 800; color: var(--brand-red); letter-spacing: -0.5px; line-height: 1.05;
  }
  /* Front */
  .card--front { display: flex; flex-direction: column; align-items: center; justify-content: center; }
  .card--front .brand-name { font-size: 46px; text-align: center; }
  .card--front .web {
    margin-top: 30px; color: var(--ink-soft); font-size: 15px; letter-spacing: 3px;
  }
  /* Back */
  .card--back .brand-block {
    position: absolute; left: 50px; top: 96px; width: 240px;
  }
  .card--back .brand-name { font-size: 32px; }
  .card--back .divider {
    position: absolute; left: 318px; top: 78px; width: 1px; height: 150px; background: var(--divider);
  }
  .contact { position: absolute; left: 340px; top: 70px; color: var(--ink-white); }
  .contact .person { font-size: 17px; font-weight: 700; }
  .contact .role { font-size: 14px; color: var(--ink-soft); margin-bottom: 12px; }
  .contact .line { display: flex; align-items: center; gap: 8px; font-size: 13px; line-height: 22px; }
  .contact .line svg { width: 13px; height: 13px; flex: none; }
  .contact .address { margin-top: 10px; font-size: 13px; line-height: 20px; }
  .card--back .band {
    position: absolute; left: 0; right: 0; bottom: 26px; height: 10px;
    background: linear-gradient(90deg, var(--band-light), var(--brand-red));
  }
</style>
</head>
<body>
<main class="stage">
  <section class="card card--front" aria-label="Business card front">
    <div class="brand-name">Brell Stone Company</div>
    <div class="web">www.brellstone-example.com</div>
  </section>

  <section class="card card--back" aria-label="Business card back">
    <div class="brand-block"><div class="brand-name">Brell Stone Company</div></div>
    <div class="divider"></div>
    <div class="contact">
      <div class="person">Dana Morell</div>
      <div class="role">President</div>
      <div class="line">
        <svg viewBox="0 0 16 16" fill="var(--brand-red)"><path d="M3 1h3l1.5 4-2 1.2a9 9 0 0 0 4.3 4.3L11 8.5l4 1.5v3a2 2 0 0 1-2 2A12 12 0 0 1 1 3a2 2 0 0 1 2-2z"/></svg>
        (555) 014-2290
      </div>
      <div class="line">
        <svg viewBox="0 0 16 16"><rect x="1" y="3" width="14" height="10" fill="var(--brand-red)"/><path d="M1 3l7 6 7-6" fill="none" stroke="#111" stroke-width="1.4"/></svg>
        info@brellstone-example.com
      </div>
      <div class="line">
        <svg viewBox="0 0 16 16" fill="none" stroke="var(--brand-red)" stroke-width="1.4"><circle cx="8" cy="8" r="6.5"/><ellipse cx="8" cy="8" rx="3" ry="6.5"/><path d="M1.5 8h13"/></svg>
        www.brellstone-example.com
      </div>
      <div class="address">48 Harbor Works Lane<br>Millbrook, NY 10000</div>
    </div>
    <div class="band"></div>
  </section>
</main>
</body>
</html>
```